Verpackungsdesign für Pasta aus Buchweizen
Zielgruppe
Unser Unternehmen VELMORIA sucht ein sehr modernes Verpackungsdesign für Pasta aus Buchweizen.
Unsere Produkte sind in unserem Online Shop und unterscheiden sich durch die herkömmliche Pasta, da wir Buchweizen in die Verarbeitung mit aufnehmen und somit die gesundheitsfördernde Eigenschaft des Buchweizens im Vordergrund steht. Unsere Pasta aus Buchweizenmehl mit klassischem Hartweizengrieß ist in dieser Form noch nicht im stationären Handel erhältlich, deshalb wünschen wir uns ein neues, ansprechendes Verpackungsdesign welches von den Massenprodukten aus den Regalen im Handel heraussticht. Das Design sollte also minimalistisch und sehr modern wirken, und sich deutlich von der Konkurrenz abheben.
Die Zielgruppe richtet sich sowohl an Massen die Pasta in allen Variationen lieben, als auch an ernährungsbewusste Veganer/Vegetarier die Alternativen im Bereich der herkömmlichen Pasta Kochkultur suchen.
PS: Mit dem Verkauf unserer Pasta investieren wir außerdem in den Aufbau und der Infrastruktur des Erzeugerlandes. Durch unser Prinzip „Teilen & Wachsen“ fördern wir mit unseren Gewinnen nachhaltige Projekte in den Erzeugerländern und helfen somit wirtschaftlich benachteiligten Regionen auf der Welt. (Fair Trade)
Aufgabenstellung
Wir besitzen bereits ein Logo und Verpackungen für unsere Pasta Sorten. Das Logo und das Grundgerüst der Stanzform / Verpackungsmaße (inkl. Sichtfenster) soll beibehalten werden (Siehe Anhang). Als Pasta Verpackungen benutzen wir Faltschachteln und Banderolen.
Verpackungsmaße:
- Faltschachtel (90 x 40 x 165 mm)
- Banderole (560 x 70mm)
Der Produktname ist je nach Sorte zu präzisieren:
- Fusilli
- Makkaroni
- Bandnudeln
- Tarhana
Produktgewicht:
- 250g
Eigenschaften:
- Buchweizenmehl
- 100% Vegan
- Kochzeit 3 Minuten
- Liebevolle Handarbeit
WICHTIG:
1) Bitte benutzt die hochgeladene, leere Stanzform für Artwork.
2) Die Designfarbe kann anhand des Aufstellers ausgerichtet werden (CMYK: 0, 20, 32, 0 und 60, 57, 56, 62) es ist aber kein muss und ihr seit frei in der Kreativität.
3) Bitte das Sichtfenster mit Rand wie aktuell auf den Produkten übernehmen (siehe www.velmoria.de/shop)
Nach dem Wettbewerb planen wir zusätzlich ein 1zu1 Projekt und würden uns freuen einen Gewinner auszuwählen - Wir freuen uns auf eure Ideen :)

```html
<!DOCTYPE html>
<html lang="de">
<head>
<meta charset="utf-8">
<title>VELMORIA – Buchweizen Pasta Verpackungen</title>
<link rel="stylesheet" href="https://fonts.googleapis.com/css2?family=Montserrat:wght@200;300;400;500&family=Oswald:wght@200;300;400;600&display=swap">
<style>
  :root {
    --stage-top: #474747;
    --stage-mid: #5a5a5a;
    --stage-bottom: #707070;
    --box-dark: #232323;
    --box-side: #1d1d1d;
    --box-band: #2e2e2e;
    --ink-light: #e6e6e6;
    --ink-soft: #bdbdbd;
    --ink-muted: #9a9a9a;
    --ink-dark: #141414;
    --window-rim: #3a3a3a;
    --vegan-green: #4f9a3a;
  }
  * { box-sizing: border-box; margin: 0; padding: 0; }
  html, body { width: 1200px; height: 3250px; overflow: hidden; background: #ffffff; }
  body { position: relative; font-family: "Montserrat", Arial, sans-serif; }

  .stage {
    position: absolute; left: 82px; width: 1036px; height: 990px;
    background: linear-gradient(180deg, var(--stage-top) 0%, var(--stage-top) 30%, var(--stage-mid) 55%, var(--stage-bottom) 100%);
    overflow: hidden;
  }
  .stage--fusilli { top: 80px; }
  .stage--makkaroni { top: 1128px; }
  .stage--tarhana { top: 2198px; }

  .stage-caption {
    position: absolute; left: 602px; top: 330px;
    font-weight: 200; font-size: 34px; line-height: 42px; letter-spacing: 0.42em;
    color: var(--ink-light);
  }

  .carton { position: absolute; left: 120px; top: 150px; height: 720px; display: flex; box-shadow: 0 30px 40px rgba(0,0,0,0.35); }

  .carton-side {
    position: relative; width: 120px; height: 100%;
    background: var(--box-side); color: var(--ink-soft);
    padding: 160px 12px 0;
  }
  .cook-time { font-size: 13px; font-weight: 300; line-height: 17px; text-transform: uppercase; }
  .cook-time strong { font-weight: 400; display: block; }
  .cook-icon { display: block; margin: 22px 0 0 10px; }
  .side-copy { margin-top: 36px; font-size: 7.5px; line-height: 10px; font-weight: 300; color: var(--ink-muted); }
  .side-copy p + p { margin-top: 12px; }
  .vegan-badge {
    position: absolute; left: 38px; top: 580px;
    width: 46px; height: 46px; border-radius: 50%;
    background: var(--vegan-green); border: 2px solid #d8ecd0;
  }
  .side-weight { position: absolute; left: 38px; top: 665px; font-size: 13px; font-weight: 300; }

  .carton-front {
    position: relative; width: 345px; height: 100%;
    background: var(--box-dark); overflow: hidden;
  }
  .front-band { position: absolute; top: 0; right: 0; width: 110px; height: 100%; background: var(--box-band); }
  .brand {
    position: absolute; left: 0; right: 0; top: 50px;
    display: flex; align-items: center; justify-content: center; gap: 8px;
    font-family: "Oswald", Arial, sans-serif; font-weight: 400;
    font-size: 20px; letter-spacing: 0.02em; color: #ffffff;
  }
  .brand-dot { width: 10px; height: 10px; border-radius: 50%; background: #ffffff; }
  .product-title {
    position: absolute; left: 62px; top: 150px;
    font-family: "Oswald", Arial, sans-serif; font-weight: 200;
    font-size: 50px; line-height: 52px; color: var(--ink-light);
  }
  .product-sub {
    position: absolute; left: 64px; top: 262px;
    font-size: 14px; font-weight: 300; letter-spacing: 0.3em; color: var(--ink-soft);
  }
  .window {
    position: absolute; left: 58px; top: 410px; width: 176px; height: 210px;
    border: 4px solid var(--window-rim); border-radius: 14px;
  }
  .window--fusilli { background: linear-gradient(135deg, #c99a5c, #7a4f26); }
  .window--makkaroni { background: linear-gradient(135deg, #d3a36a, #8a5a2e); }
  .window--tarhana { background: linear-gradient(135deg, #d9854a, #8a3e1c); }
  .variety { position: absolute; left: 250px; top: 420px; }
  .variety-name { font-family: "Oswald", Arial, sans-serif; font-weight: 400; font-size: 30px; letter-spacing: 1.8px; fill: var(--ink-dark); }
  .variety-note { font-family: "Montserrat", Arial, sans-serif; font-weight: 300; font-size: 10px; fill: var(--ink-soft); }
  .front-weight { position: absolute; right: 32px; bottom: 72px; font-size: 18px; font-weight: 300; color: var(--ink-soft); }
</style>
</head>
<body>

<section class="stage stage--fusilli">
  <div class="carton">
    <div class="carton-side">
      <p class="cook-time">Kochzeit<strong>3 Minuten</strong></p>
      <svg class="cook-icon" width="64" height="62" viewBox="0 0 64 62" fill="none" stroke="#e6e6e6" stroke-width="2">
        <path d="M8 22 H48 V38 a6 6 0 0 1 -6 6 H14 a6 6 0 0 1 -6 -6 Z"/>
        <path d="M4 24 H8 M48 24 H52 M22 22 V18 H34 V22"/>
        <path d="M12 32 q4 -3 8 0 t8 0 t8 0 t8 0"/>
        <path d="M46 14 q4 -4 0 -8 M52 16 q4 -4 0 -8"/>
        <path d="M18 50 q2 4 0 6 q-2 -2 0 -6 M28 50 q2 4 0 6 q-2 -2 0 -6 M38 50 q2 4 0 6 q-2 -2 0 -6"/>
      </svg>
      <div class="side-copy">
        <p>Buchweizen trifft Hartweizengrieß – fein, nussig und bissfest.</p>
        <p>Nudeln in sprudelnd kochendes Salzwasser geben und drei Minuten garen.</p>
        <p>Zutaten: Buchweizenmehl, Hartweizengrieß, Wasser. Kühl und trocken lagern. Nach dem Öffnen gut verschließen und bald verbrauchen.</p>
      </div>
      <div class="vegan-badge"></div>
      <p class="side-weight">250g ℮</p>
    </div>
    <div class="carton-front">
      <div class="front-band"></div>
      <div class="brand"><span class="brand-dot"></span>VELMORIA</div>
      <h2 class="product-title">BUCHWEIZEN<br>PASTA</h2>
      <p class="product-sub">BUCKWHEAT</p>
      <div class="window window--fusilli" role="img" aria-label="Sichtfenster mit Blick auf Buchweizen-Fusilli"></div>
      <svg class="variety" width="60" height="200" viewBox="0 0 60 200">
        <text class="variety-name" transform="translate(42 200) rotate(-90)">FUSILLI</text>
      </svg>
      <p class="front-weight">250g ℮</p>
    </div>
  </div>
  <p class="stage-caption">BUCHWEIZEN<br>PASTA</p>
</section>

<section class="stage stage--makkaroni">
  <div class="carton">
    <div class="carton-side">
      <p class="cook-time">Kochzeit<strong>3 Minuten</strong></p>
      <svg class="cook-icon" width="64" height="62" viewBox="0 0 64 62" fill="none" stroke="#e6e6e6" stroke-width="2">
        <path d="M8 22 H48 V38 a6 6 0 0 1 -6 6 H14 a6 6 0 0 1 -6 -6 Z"/>
        <path d="M4 24 H8 M48 24 H52 M22 22 V18 H34 V22"/>
        <path d="M12 32 q4 -3 8 0 t8 0 t8 0 t8 0"/>
        <path d="M46 14 q4 -4 0 -8 M52 16 q4 -4 0 -8"/>
        <path d="M18 50 q2 4 0 6 q-2 -2 0 -6 M28 50 q2 4 0 6 q-2 -2 0 -6 M38 50 q2 4 0 6 q-2 -2 0 -6"/>
      </svg>
      <div class="side-copy">
        <p>Buchweizen trifft Hartweizengrieß – fein, nussig und bissfest.</p>
        <p>Nudeln in sprudelnd kochendes Salzwasser geben und drei Minuten garen.</p>
        <p>Zutaten: Buchweizenmehl, Hartweizengrieß, Wasser. Kühl und trocken lagern. Nach dem Öffnen gut verschließen und bald verbrauchen.</p>
      </div>
      <div class="vegan-badge"></div>
      <p class="side-weight">250g ℮</p>
    </div>
    <div class="carton-front">
      <div class="front-band"></div>
      <div class="brand"><span class="brand-dot"></span>VELMORIA</div>
      <h2 class="product-title">BUCHWEIZEN<br>PASTA</h2>
      <p class="product-sub">BUCKWHEAT</p>
      <div class="window window--makkaroni" role="img" aria-label="Sichtfenster mit Blick auf Buchweizen-Makkaroni"></div>
      <svg class="variety" width="60" height="200" viewBox="0 0 60 200">
        <text class="variety-name" transform="translate(42 200) rotate(-90)">MAKKARONI</text>
      </svg>
      <p class="front-weight">250g ℮</p>
    </div>
  </div>
  <p class="stage-caption">BUCHWEIZEN<br>PASTA</p>
</section>

<section class="stage stage--tarhana">
  <div class="carton">
    <div class="carton-side">
      <p class="cook-time">Kochzeit<strong>3 Minuten</strong></p>
      <svg class="cook-icon" width="64" height="62" viewBox="0 0 64 62" fill="none" stroke="#e6e6e6" stroke-width="2">
        <path d="M8 22 H48 V38 a6 6 0 0 1 -6 6 H14 a6 6 0 0 1 -6 -6 Z"/>
        <path d="M4 24 H8 M48 24 H52 M22 22 V18 H34 V22"/>
        <path d="M12 32 q4 -3 8 0 t8 0 t8 0 t8 0"/>
        <path d="M46 14 q4 -4 0 -8 M52 16 q4 -4 0 -8"/>
        <path d="M18 50 q2 4 0 6 q-2 -2 0 -6 M28 50 q2 4 0 6 q-2 -2 0 -6 M38 50 q2 4 0 6 q-2 -2 0 -6"/>
      </svg>
      <div class="side-copy">
        <p>Buchweizen trifft Hartweizengrieß – fein, nussig und bissfest.</p>
        <p>Nudeln in sprudelnd kochendes Salzwasser geben und drei Minuten garen.</p>
        <p>Zutaten: Buchweizenmehl, Hartweizengrieß, Wasser. Kühl und trocken lagern. Nach dem Öffnen gut verschließen und bald verbrauchen.</p>
      </div>
      <div class="vegan-badge"></div>
      <p class="side-weight">250g ℮</p>
    </div>
    <div class="carton-front">
      <div class="front-band"></div>
      <div class="brand"><span class="brand-dot"></span>VELMORIA</div>
      <h2 class="product-title">BUCHWEIZEN<br>PASTA</h2>
      <p class="product-sub">BUCKWHEAT</p>
      <div class="window window--tarhana" role="img" aria-label="Sichtfenster mit Blick auf Buchweizen-Tarhana"></div>
      <svg class="variety" width="60" height="200" viewBox="0 0 60 200">
        <text class="variety-note" transform="translate(14 120) rotate(-90)">für Suppen</text>
        <text class="variety-name" transform="translate(42 200) rotate(-90)">TARHANA</text>
      </svg>
      <p class="front-weight">250g ℮</p>
    </div>
  </div>
  <p class="stage-caption">BUCHWEIZEN<br>PASTA</p>
</section>

</body>
</html>
```